Quran Jar

So I need help designing bespoke jars which will contain religious quotes.

So there will be three jars in total sold either individually or in two or as a three.

Each Jar will have different contents and preferably a different colour scheme.

I want the packaging to be customised with my branding and logo and to make the product stand out I am thinking of packing it further in a cotton bag with my branding.

```html
<!DOCTYPE html>
<html lang="en">
<head>
<meta charset="utf-8">
<title>Quran Jar – Lid Design</title>
<link href="https://fonts.googleapis.com/css2?family=Poppins:wght@500&family=Josefin+Sans:wght@300&display=swap" rel="stylesheet">
<style>
  :root {
    --backdrop: #e4e4e4;
    --lid-white: #f6f6f6;
    --band-green: #405f4c;
    --brand-gold: #e6cd85;
    --ink: #3a3a3a;
    --rule: #6a6a6a;
  }
  * { margin: 0; padding: 0; box-sizing: border-box; }
  html, body {
    width: 1200px;
    height: 790px;
    overflow: hidden;
    background: var(--backdrop);
  }
  .canvas {
    width: 1200px;
    height: 790px;
    display: flex;
    align-items: center;
    justify-content: center;
  }
  .lid {
    width: 900px;
    height: 560px;
    background: var(--lid-white);
    display: flex;
    flex-direction: column;
    box-shadow: 0 2px 6px rgba(0,0,0,0.08);
  }
  .brand-band {
    height: 190px;
    background: var(--band-green);
    display: flex;
    align-items: center;
    justify-content: center;
    gap: 14px;
  }
  .brand-dot {
    width: 22px;
    height: 22px;
    border-radius: 50%;
    background: var(--brand-gold);
  }
  .brand-name {
    font-family: "Poppins", sans-serif;
    font-weight: 500;
    font-size: 34px;
    color: var(--brand-gold);
    letter-spacing: 0.5px;
  }
  .product-line {
    flex: 1;
    display: flex;
    align-items: center;
    justify-content: center;
    gap: 34px;
    padding-bottom: 120px;
  }
  .product {
    font-family: "Josefin Sans", sans-serif;
    font-weight: 300;
    color: var(--ink);
    text-align: center;
    line-height: 1;
  }
  .product-title {
    font-size: 40px;
    letter-spacing: 1px;
  }
  .product-sub {
    font-size: 15px;
    letter-spacing: 1px;
    margin-top: 2px;
  }
  .divider {
    width: 1px;
    height: 72px;
    background: var(--rule);
  }
</style>
</head>
<body>
  <main class="canvas">
    <section class="lid">
      <header class="brand-band">
        <span class="brand-dot"></span>
        <span class="brand-name">Quiet Verse</span>
      </header>
      <div class="product-line">
        <div class="product">
          <div class="product-title">QURAN</div>
          <div class="product-sub">JAR</div>
        </div>
        <span class="divider"></span>
        <div class="product">
          <div class="product-title">DUA</div>
          <div class="product-sub">JAR</div>
        </div>
      </div>
    </section>
  </main>
</body>
</html>
```